Business Card for my New Brokerage

Looking to get a business card design for my new Real Estate Brokerage.
I want it with Picture, Phone Number, Email, Website, Office Address
Name and Designation. Please add logo too.

Target Market(s)

Real Estate Investors or Home Buyers

Industry/Entity Type

Real Estate

Contact Information for Business Card

Name, Email, Phone Number, website, email, office address

Colors
EB3D1F
EC4F4E
F09395
F8D3D4
FCEDEE

Requirements
Must have
• Minimalistic, Clean, Modern, Photo
Nice to have
• White and Red Colors

```html
<!DOCTYPE html>
<html lang="en">
<head>
<meta charset="UTF-8">
<title>Ember Realty Inc – Business Card</title>
<link href="https://fonts.googleapis.com/css2?family=Montserrat:wght@400;500;700&display=swap" rel="stylesheet">
<style>
  :root {
    --page-bg: #d9d9d9;
    --card-bg: #2b2b2b;
    --card-edge: #e00000;
    --brand-red: #e00a0a;
    --gold: #c9a14a;
    --text-light: #f2f2f2;
    --photo-dark: #303030;
    --photo-light: #3d3d3d;
  }
  * { box-sizing: border-box; margin: 0; padding: 0; }
  html, body {
    width: 1200px; height: 800px; overflow: hidden;
    background: var(--page-bg);
    font-family: "Montserrat", Arial, sans-serif;
  }
  .canvas {
    width: 1200px; height: 800px;
    display: flex; flex-direction: column;
    align-items: center; justify-content: center; gap: 36px;
  }
  .card {
    position: relative;
    width: 620px; height: 354px;
    background: var(--card-bg);
    border: 2px solid var(--card-edge);
    overflow: hidden;
  }
  /* Front side */
  .card-front__photo {
    position: absolute; right: 0; top: 0;
    width: 290px; height: 100%;
    background: linear-gradient(160deg, var(--photo-light), var(--photo-dark));
  }
  .card-front__info {
    position: absolute; left: 44px; top: 40px;
    width: 300px;
  }
  .brand {
    display: flex; align-items: center; gap: 8px;
  }
  .brand__name {
    font-weight: 700; color: var(--brand-red);
    letter-spacing: 1px; text-transform: uppercase;
  }
  .brand__dot {
    width: 10px; height: 10px; border-radius: 50%;
    background: var(--gold);
  }
  .card-front .brand__name { font-size: 26px; }
  .person { margin-top: 34px; }
  .person__name {
    font-weight: 700; font-size: 20px; color: var(--gold);
    text-transform: uppercase; letter-spacing: 0.5px;
  }
  .person__title {
    font-size: 14px; color: var(--text-light); margin-top: 4px;
  }
  .address {
    margin-top: 18px; font-size: 13px; line-height: 1.45;
    color: var(--text-light); font-style: normal;
  }
  .contact-list {
    list-style: none; margin-top: 14px;
    font-size: 13px; color: var(--text-light);
  }
  .contact-list li {
    display: flex; align-items: center; gap: 10px;
    line-height: 1.55;
  }
  .contact-list svg { width: 13px; height: 13px; flex: none; }
  /* Back side */
  .card-back {
    display: flex; align-items: center; justify-content: center;
  }
  .card-back .brand__name { font-size: 44px; letter-spacing: 2px; }
  .card-back .brand__dot { width: 16px; height: 16px; }
</style>
</head>
<body>
<main class="canvas">
  <section class="card card-front">
    <div class="card-front__photo" role="img" aria-label="Portrait photo of the broker in a dark suit and white shirt"></div>
    <div class="card-front__info">
      <div class="brand">
        <span class="brand__name">Ember Realty Inc</span>
        <span class="brand__dot"></span>
      </div>
      <div class="person">
        <p class="person__name">Daniel Brooks</p>
        <p class="person__title">Founder &amp; CEO</p>
      </div>
      <address class="address">
        412 Birchwood Avenue<br>
        Juneau, Alaska 99801
      </address>
      <ul class="contact-list">
        <li>
          <svg viewBox="0 0 24 24" fill="var(--gold)" aria-hidden="true"><path d="M6.6 10.8a15.1 15.1 0 0 0 6.6 6.6l2.2-2.2c.3-.3.7-.4 1-.2 1.1.4 2.3.6 3.6.6.6 0 1 .4 1 1V20c0 .6-.4 1-1 1A17 17 0 0 1 3 4c0-.6.4-1 1-1h3.5c.6 0 1 .4 1 1 0 1.3.2 2.5.6 3.6.1.3 0 .7-.2 1z"/></svg>
          555-210-4836
        </li>
        <li>
          <svg viewBox="0 0 24 24" fill="none" stroke="var(--gold)" stroke-width="2.4" aria-hidden="true"><rect x="6" y="2" width="12" height="20" rx="2"/></svg>
          555-317-9042
        </li>
        <li>
          <svg viewBox="0 0 24 24" fill="var(--gold)" aria-hidden="true"><path d="M2 5h20v14H2z M2 5l10 8 10-8" stroke="var(--card-bg)" stroke-width="1.6"/></svg>
          hello@emberrealty.com
        </li>
        <li>
          <svg viewBox="0 0 24 24" fill="none" stroke="var(--gold)" stroke-width="2.2" aria-hidden="true"><circle cx="12" cy="12" r="10"/><path d="M2 12h20M12 2c3 3 3 17 0 20M12 2c-3 3-3 17 0 20"/></svg>
          www.emberrealty.com
        </li>
      </ul>
    </div>
  </section>

  <section class="card card-back">
    <div class="brand">
      <span class="brand__name">Ember Realty Inc</span>
      <span class="brand__dot"></span>
    </div>
  </section>
</main>
</body>
</html>
```